New web design for a service provider in the medical field

We are looking for a new design for our website. We are a company that repairs and sells medical endoscopes. Our customers include doctors and hospitals. Our current website can be found at https://lumavex.de/en/lumavex-english.
We need a new web design (without programming) for the following 3 pages:
-Startpage https://lumavex.de/en/lumavex-english/
-Used endoscopes https://lumavex.de/en/used-endoscopes/
-Purchase https://lumavex.de/en/purchase/
The design should be modern and stylish.
The blue color of the logo should be reflected on the page, but not too intrusive.
I have uploaded the images from the header. If more images are needed, let me know and I will upload them.

Target Market(s)
Doctors and hospitals

```html
<!DOCTYPE html>
<html lang="en">
<head>
<meta charset="utf-8">
<title>Lumavex – Endoscope Repair</title>
<link href="https://fonts.googleapis.com/css2?family=Outfit:wght@300;400;500;600;700;800&display=swap" rel="stylesheet">
<style>
:root{
  --navy:#1a3e66;
  --navy-deep:#173a63;
  --blue:#2a9fd8;
  --blue-mid:#2679c0;
  --blue-dark:#1b4f86;
  --ink:#1f2f44;
  --text:#4b5766;
  --pale:#eef4fa;
  --white:#ffffff;
  --line:#d8e2ec;
}
*{margin:0;padding:0;box-sizing:border-box}
html,body{width:1200px;height:4313px;overflow:hidden}
body{position:relative;background:var(--white);font-family:"Outfit",sans-serif;color:var(--ink)}
.abs{position:absolute}
a{color:inherit;text-decoration:none}

/* header */
.topbar{left:680px;top:0;width:520px;height:40px;background:var(--blue);clip-path:polygon(4% 0,100% 0,100% 100%,0 100%);display:flex;align-items:center;gap:26px;padding-left:20px;color:#fff;font-size:12px;font-weight:600}
.topbar .ico{display:inline-block;width:16px;height:16px;border-radius:50%;background:#fff;vertical-align:middle;margin-right:6px}
.brand{display:flex;align-items:center;gap:10px}
.brand-dot{width:16px;height:16px;border-radius:50%;background:var(--blue)}
.brand-name{font-size:26px;font-weight:600;color:var(--navy);letter-spacing:.2px}
.nav{left:298px;top:68px;display:flex;gap:26px;font-size:12px;font-weight:700;color:var(--navy)}
.nav .active{border-bottom:2px solid var(--blue);padding-bottom:24px}
.btn-purchase{left:988px;top:60px;width:126px;height:37px;background:var(--navy);color:#fff;font-size:12px;font-weight:700;display:flex;align-items:center;justify-content:center}

/* hero */
.hero{left:0;top:120px;width:1200px;height:667px;background:linear-gradient(120deg,#1e5f95 0%,#2b86c2 45%,#3aa3d8 100%);clip-path:polygon(0 0,100% 0,100% 85%,42% 100%,0 85%)}
.hero-photo{left:530px;top:120px;width:670px;height:600px;background:radial-gradient(circle at 55% 45%,#f2f4f6 0%,#cfd8e0 30%,rgba(40,60,80,.0) 62%);clip-path:polygon(12% 0,100% 0,100% 95%,0 100%)}
.hero-frame{left:80px;top:238px;width:129px;height:291px;border:3px solid #5bb9ea;border-right:none}
.hero-frame::after{content:"";position:absolute;right:0;top:0;width:3px;height:24px;background:#5bb9ea}
.hero-kicker{left:116px;top:288px;color:#fff;font-size:19px;letter-spacing:2px}
.hero-title{left:116px;top:318px;color:#fff;font-size:40px;font-weight:800;line-height:50px}
.btn-learn{left:119px;top:432px;width:176px;height:47px;background:var(--blue);color:#fff;font-size:15px;font-weight:600;display:flex;align-items:center;justify-content:center}

/* service */
.pale-band{left:0;top:690px;width:1200px;height:1123px;background:var(--pale);z-index:-1}
.h2{font-size:33px;font-weight:800;color:var(--navy-deep);text-align:center;width:1200px;left:0}
.intro{left:220px;top:918px;width:760px;text-align:center;font-size:18px;line-height:28px;color:var(--text)}
.hex{width:310px;height:355px;color:#fff;text-align:center}
.hex svg.shape{position:absolute;left:0;top:0}
.hex .in{position:absolute;left:28px;right:28px;top:88px}
.hex h3{font-size:19px;font-weight:700;margin-top:10px}
.hex .sub{font-size:14px}
.hex p{font-size:11.5px;line-height:14px;margin-top:6px}

/* about */
.about-photo{left:67px;top:1587px;width:737px;height:477px;background:linear-gradient(135deg,#bfe6f4,#5fc1e6 45%,#2c6f99 100%);clip-path:polygon(15% 0,100% 0,100% 100%,0 100%)}
.about-card{left:571px;top:1625px;width:524px;height:385px;background:#fff;box-shadow:0 6px 30px rgba(30,60,100,.12);padding:48px 48px}
.about-card h3{font-size:22px;font-weight:600;line-height:28px;color:var(--navy-deep)}
.about-card .rule{width:66px;height:2px;background:var(--blue);margin:18px 0 22px}
.about-card p{font-size:13px;line-height:18px;color:var(--text);margin-bottom:12px}
.about-bar{left:905px;top:2010px;width:190px;height:10px;background:var(--blue)}

/* faulty */
.faulty{left:0;top:2198px;width:1200px;height:472px;background:linear-gradient(110deg,#2a8fd0,#3ab0e4)}
.faulty-photo{left:536px;top:2159px;width:609px;height:419px;background:linear-gradient(135deg,#f4f6f8,#dfe5ea 50%,#9aa8b4);clip-path:polygon(14% 0,100% 0,84% 100%,0 100%)}
.faulty-title{left:122px;top:2286px;color:#fff;font-size:31px;font-weight:300}
.faulty-title b{font-weight:800}
.faulty-sub{left:122px;top:2354px;color:#fff;font-size:22px}
.faulty-text{left:124px;top:2406px;width:400px;color:#eaf6fd;font-size:15px;line-height:25px}
.btn-order{left:124px;top:2506px;width:179px;height:50px;background:var(--navy);color:#fff;font-size:15px;font-weight:600;display:flex;align-items:center;justify-content:center;gap:6px}

/* values */
.ring{left:453px;top:2897px;width:292px;height:292px;border-radius:50%;border:2px solid #7cc7ee;padding:10px}
.ring div{width:100%;height:100%;border-radius:50%;background:radial-gradient(circle,#5a6168 0%,#9aa0a6 40%,#eef0f2 75%)}
.value{width:260px}
.value h4{font-size:18px;font-weight:600;color:var(--navy-deep);line-height:20px}
.value p{font-size:14px;line-height:19px;color:var(--text);margin-top:6px}
.value.left{text-align:right}
.vicon{width:48px;height:48px}
.vdiv{height:1px;background:var(--line)}

/* help */
.help{left:0;top:3336px;width:1200px;height:601px;background:linear-gradient(90deg,#bfe3f2,#e8f3fa 55%,#e8f3fa)}
.help-photo{left:0;top:3336px;width:600px;height:601px;background:linear-gradient(160deg,#a9dbee,#58b7e0 50%,#9fd2ea)}
.form{left:618px;top:3489px;width:478px;height:368px;background:linear-gradient(135deg,#2a8fd0,#34a4dd)}
.field{left:35px;width:408px;height:47px;border:1px solid rgba(255,255,255,.7);color:#fff;font-size:13px;font-weight:600;display:flex;align-items:center;gap:8px;padding-left:18px}
.field.area{align-items:flex-start;padding-top:12px;height:82px}
.fi{width:13px;height:13px;border-radius:50%;background:#fff}
.btn-send{left:34px;top:282px;width:165px;height:47px;background:var(--navy);color:#fff;font-size:12px;font-weight:700;display:flex;align-items:center;justify-content:center}

/* footer */
.foot-text{left:122px;top:4090px;width:260px;font-size:12px;line-height:15px;color:var(--text)}
.fcol{top:4010px;border-left:2px solid var(--blue);padding-left:18px;height:120px}
.fcol h5{font-size:14px;font-weight:700;color:var(--navy-deep);margin-bottom:16px}
.fcol li{list-style:none;font-size:13px;color:var(--text);line-height:29px}
.social{display:flex;gap:6px;margin-top:10px}
.social span{width:29px;height:29px;border-radius:50%;background:var(--navy)}
.copy{left:0;top:4240px;width:1200px;border-top:1px solid var(--line);text-align:center;padding-top:26px;font-size:12px;color:var(--text)}
</style>
</head>
<body>

<!-- Header -->
<div class="abs topbar">
  <span><span class="ico"></span>info@lumavex.de</span>
  <span><span class="ico"></span>+49 4100 555 012-0</span>
  <span>ENG ▾</span>
</div>
<div class="abs" style="left:96px;top:38px">
  <div class="brand"><span class="brand-dot"></span><span class="brand-name">Lumavex</span></div>
</div>
<nav class="abs nav">
  <a class="active">ENDOSCOPE REPAIR</a>
  <a>ENDOSCOPY SYSTEMS</a>
  <a>ENDOSCOPY ACCESSORIES</a>
  <a>ACCESSORIES CATALOG</a>
</nav>
<a class="abs btn-purchase">PURCHASE</a>

<!-- Hero -->
<div class="abs pale-band"></div>
<div class="abs hero"></div>
<div class="abs hero-photo" role="img" aria-label="Photo of flexible endoscopes in white holders"></div>
<div class="abs hero-frame"></div>
<div class="abs hero-kicker">WELCOME TO LUMAVEX</div>
<h1 class="abs hero-title">PUT YOUR ENDOSCOPE<br>IN RELIABLE HANDS!</h1>
<a class="abs btn-learn">LEARN MORE</a>
<svg class="abs" style="left:586px;top:567px" width="28" height="62" viewBox="0 0 28 62" fill="none" stroke="#fff" stroke-width="2">
  <rect x="4" y="1" width="20" height="32" rx="10"/><line x1="14" y1="8" x2="14" y2="14"/>
  <polyline points="8,42 14,48 20,42"/><polyline points="8,52 14,58 20,52"/>
</svg>

<!-- Service -->
<h2 class="abs h2" style="top:846px">YOUR FUTURE OUR SERVICE</h2>
<p class="abs intro">Lumavex GmbH is specialised in the repair and sale of Orvane, Pextora and Fujara flexible medical endoscopes. As a service-oriented company, we are at your side with our knowledge and skills!</p>
<svg class="abs" style="left:270px;top:1030px" width="660" height="85" fill="none" stroke="#2a9fd8" stroke-width="2">
  <line x1="330" y1="0" x2="330" y2="41"/>
  <polyline points="10,76 10,41 646,41 646,76"/>
  <line x1="330" y1="41" x2="330" y2="76"/>
  <circle cx="10" cy="78" r="5" stroke="#1a3e66" stroke-width="3"/>
  <circle cx="330" cy="78" r="5" stroke="#1a3e66" stroke-width="3"/>
  <circle cx="646" cy="78" r="5" stroke="#1a3e66" stroke-width="3"/>
</svg>

<div class="abs hex" style="left:127px;top:1148px">
  <svg class="shape" width="310" height="355"><polygon points="155,0 310,89 310,266 155,355 0,266 0,89" fill="#2a9fd8"/></svg>
  <div class="in" style="top:80px">
    <svg width="60" height="44" fill="none" stroke="#fff" stroke-width="2"><circle cx="20" cy="22" r="14"/><circle cx="20" cy="22" r="8"/><rect x="32" y="26" width="22" height="7"/></svg>
    <h3>REPAIR</h3>
    <div class="sub">Endoscope repair service</div>
    <p style="font-size:13px">Manufacturer-independent we repair and maintain endoscopes, individual components</p>
  </div>
  <svg class="abs" style="left:136px;top:273px" width="40" height="40" fill="none" stroke="#fff" stroke-width="2"><circle cx="20" cy="20" r="18"/><polyline points="13,17 20,24 27,17"/></svg>
</div>
<div class="abs hex" style="left:447px;top:1148px">
  <svg class="shape" width="310" height="355"><polygon points="155,0 310,89 310,266 155,355 0,266 0,89" fill="#1b4f86"/></svg>
  <div class="in" style="top:74px">
    <svg width="44" height="60" fill="none" stroke="#fff" stroke-width="2"><rect x="14" y="8" width="16" height="26" rx="3"/><line x1="22" y1="34" x2="22" y2="58"/><circle cx="22" cy="18" r="4"/></svg>
    <h3>PURCHASE</h3>
    <div class="sub">Used endoscopes</div>
    <p>We are very interested in buying your old endoscopes – even defective and dismantled! We offer fair conditions! Please contact us for a purchase offer!</p>
  </div>
  <svg class="abs" style="left:135px;top:282px" width="40" height="40" fill="none" stroke="#fff" stroke-width="2"><circle cx="20" cy="20" r="18"/><polyline points="13,17 20,24 27,17"/></svg>
</div>
<div class="abs hex" style="left:772px;top:1148px">
  <svg class="shape" width="310" height="355"><polygon points="155,0 310,89 310,266 155,355 0,266 0,89" fill="#2679c0"/></svg>
  <div class="in" style="top:64px">
    <svg width="50" height="46" fill="none" stroke="#fff" stroke-width="2"><circle cx="30" cy="22" r="14"/><rect x="8" y="10" width="10" height="18"/></svg>
    <h3>SALE</h3>
    <div class="sub">Used endoscopes</div>
    <p style="font-size:10.5px;line-height:13px">Our regular stock includes refurbished gastroscopes, coloscopes, bronchoscopes, cystoscopes and duodenoscopes from the well-known manufacturers Orvane, Pextora and Fujara.</p>
  </div>
  <svg class="abs" style="left:135px;top:282px" width="40" height="40" fill="none" stroke="#fff" stroke-width="2"><circle cx="20" cy="20" r="18"/><polyline points="13,17 20,24 27,17"/></svg>
</div>

<!-- About -->
<div class="abs about-photo" role="img" aria-label="Photo of a technician in protective clothing holding an endoscope"></div>
<svg class="abs" style="left:960px;top:1880px" width="185" height="185" fill="#9bcbe9">
  <circle cx="176" cy="6" r="2"/><circle cx="176" cy="24" r="2"/><circle cx="176" cy="42" r="2"/><circle cx="176" cy="60" r="2"/><circle cx="176" cy="78" r="2"/><circle cx="176" cy="96" r="2"/><circle cx="176" cy="114" r="2"/><circle cx="176" cy="132" r="2"/><circle cx="176" cy="150" r="2"/><circle cx="176" cy="168" r="2"/>
  <circle cx="158" cy="6" r="2"/><circle cx="158" cy="24" r="2"/><circle cx="158" cy="42" r="2"/><circle cx="158" cy="60" r="2"/><circle cx="158" cy="78" r="2"/><circle cx="158" cy="96" r="2"/><circle cx="158" cy="114" r="2"/><circle cx="158" cy="132" r="2"/><circle cx="158" cy="150" r="2"/><circle cx="158" cy="168" r="2"/>
  <circle cx="2" cy="150" r="2"/><circle cx="20" cy="150" r="2"/><circle cx="38" cy="150" r="2"/><circle cx="56" cy="150" r="2"/><circle cx="74" cy="150" r="2"/><circle cx="92" cy="150" r="2"/><circle cx="110" cy="150" r="2"/><circle cx="128" cy="150" r="2"/><circle cx="140" cy="150" r="2"/>
  <circle cx="2" cy="168" r="2"/><circle cx="20" cy="168" r="2"/><circle cx="38" cy="168" r="2"/><circle cx="56" cy="168" r="2"/><circle cx="74" cy="168" r="2"/><circle cx="92" cy="168" r="2"/><circle cx="110" cy="168" r="2"/><circle cx="128" cy="168" r="2"/><circle cx="140" cy="168" r="2"/>
</svg>
<div class="abs about-bar"></div>
<div class="abs about-card">
  <h3>Endoscope repairs and second hand endoscopes from Lumavex&nbsp; cause the outcome matters!</h3>
  <div class="rule"></div>
  <p>Lumavex is a privileged partner for the start-up facility or optimisation of existing healthcare facilities, doctor's offices and hospitals. The quality and reliability of our products and our offered service are our best advertisement!</p>
  <p>As a result of optimised processes and highly qualified specialists in our company, we can work very quickly and with high quality for your benefit of least possible restrictions in your doctor's office or in your hospital.</p>
</div>

<!-- Faulty -->
<div class="abs faulty"></div>
<div class="abs faulty-photo" role="img" aria-label="Photo of several flexible endoscopes lined up on a white surface"></div>
<h2 class="abs faulty-title">FAULTY <b>ENDOSCOPE?</b></h2>
<div class="abs faulty-sub">We ensure quick and smooth repairs!</div>
<p class="abs faulty-text">Lorem ipsum dolor sit amet, consectetur adipiscing elit, sed do eiusmod tempor incididunt ut labore et dolore magna aliqua. Ut enim ad minim</p>
<a class="abs btn-order">PLACE ORDER <span>›</span></a>

<!-- Values -->
<h2 class="abs h2" style="top:2748px">CAUSE THE OUTCOME MATTERS</h2>
<div class="abs ring"><div role="img" aria-label="Photo of an endoscope control head"></div></div>

<div class="abs value left" style="left:107px;top:2862px"><h4>One company for<br>everyone</h4><p>We are a service provider for<br>doctors and hospitals!</p></div>
<svg class="abs vicon" style="left:386px;top:2876px" fill="none" stroke="#2a9fd8" stroke-width="2"><circle cx="24" cy="24" r="18"/><circle cx="24" cy="20" r="5"/></svg>
<div class="abs vdiv" style="left:150px;top:2968px;width:280px"></div>
<div class="abs value left" style="left:107px;top:3008px"><h4>Guaranteed service</h4><p>You receive a six-month warranty on all repairs!</p></div>
<svg class="abs vicon" style="left:380px;top:3013px" fill="none" stroke="#2a9fd8" stroke-width="2"><path d="M24 4 L40 10 V24 C40 34 32 40 24 44 C16 40 8 34 8 24 V10 Z"/><polyline points="16,24 22,30 32,18"/></svg>
<div class="abs vdiv" style="left:150px;top:3108px;width:280px"></div>
<div class="abs value left" style="left:107px;top:3146px"><h4>Experience<br>characterises us</h4><p>Our team has many years of experience in the business field!</p></div>
<svg class="abs vicon" style="left:385px;top:3150px" fill="none" stroke="#2a9fd8" stroke-width="2"><circle cx="24" cy="14" r="7"/><rect x="6" y="30" width="14" height="14"/><rect x="28" y="30" width="14" height="14"/></svg>

<svg class="abs vicon" style="left:790px;top:2876px" fill="none" stroke="#2a9fd8" stroke-width="2"><rect x="14" y="4" width="16" height="24" rx="3"/><line x1="22" y1="28" x2="22" y2="46"/></svg>
<div class="abs value" style="left:867px;top:2878px"><h4>The product is close<br>to our hearts</h4><p>We repair and sell second hand,<br>flexible endoscopes!</p></div>
<div class="abs vdiv" style="left:800px;top:2970px;width:285px"></div>
<svg class="abs vicon" style="left:790px;top:3013px" fill="none" stroke="#2a9fd8" stroke-width="2"><path d="M20 4 L34 9 V20 C34 28 28 33 20 36 C12 33 6 28 6 20 V9 Z"/><circle cx="34" cy="34" r="7"/></svg>
<div class="abs value" style="left:867px;top:3016px;width:270px"><h4>Services for everyone</h4><p>Our service includes the manufacturers Orvane, Pextora and Fujara!</p></div>
<div class="abs vdiv" style="left:800px;top:3110px;width:285px"></div>
<svg class="abs vicon" style="left:786px;top:3152px" fill="none" stroke="#2a9fd8" stroke-width="2"><polygon points="28,4 31,12 40,12 33,17 36,25 28,20 20,25 23,17 16,12 25,12"/><path d="M4 38 C14 32 24 42 44 30"/></svg>
<div class="abs value" style="left:867px;top:3161px"><h4>Quality not quantity</h4><p>Reliability and durability instead<br>of inferior replacements!</p></div>

<!-- Help -->
<div class="abs help"></div>
<div class="abs help-photo" role="img" aria-label="Photo of a technician in protective clothing holding an endoscope"></div>
<h2 class="abs" style="left:0;top:3392px;width:1195px;text-align:center;font-size:33px;font-weight:800;color:var(--navy-deep)">HOW CAN WE HELP YOU?</h2>
<div class="abs" style="left:537px;top:3437px;width:108px;height:3px;background:var(--blue)"></div>
<form class="abs form">
  <div class="abs field" style="top:33px"><span class="fi"></span>Name</div>
  <div class="abs field" style="top:88px"><span class="fi"></span>Phone number</div>
  <div class="abs field" style="top:142px"><span class="fi"></span>Email address</div>
  <div class="abs field area" style="top:195px">Comments</div>
  <a class="abs btn-send">SEND MESSAGE ›</a>
</form>

<!-- Footer -->
<div class="abs" style="left:130px;top:4040px">
  <div class="brand"><span class="brand-dot"></span><span class="brand-name" style="font-size:24px">Lumavex</span></div>
</div>
<p class="abs foot-text">Lorem ipsum dolor sit amet, consectetur adipiscing elit, sed do eiusmod tempor incididunt ut labore et dolore</p>
<div class="abs fcol" style="left:465px"><h5>NAVIGATION</h5><ul><li>Home</li><li>Endoscope Repair</li><li>Used Endoscope</li><li>Endoscopy Systems</li></ul></div>
<div class="abs fcol" style="left:705px"><h5>RESOURCES</h5><ul><li>Endoscopy Accesories</li><li>Purchase</li><li>Contact Us</li></ul></div>
<div class="abs fcol" style="left:912px;height:40px"><h5 style="margin-bottom:0">FOLLOW US</h5><div class="social" aria-label="Social media links"><span></span><span></span><span></span><span></span></div></div>
<div class="abs copy">© 2022 Lumavex GmbH All Right Reserved</div>

</body>
</html>
```